"Velmora Crest" sexual performance enhancement pill bottle label needed.

This should be interesting...

I am starting a line of sexual performance enhancement products. This will be the first of several products basically. Keep in mind, I am the type of business person to stay with one company for years if they provide me with quality work.

This particular product is a male sexual performance pill. The name of the product is "Velmora Crest." The packaging of the pills are a black bottle with a white top. Label on the product example would be perfect but at a minimum I have attached a "template" for your guidance.

Some of the technical aspects of this are as follows:

-File Format: Illustrator CS6 is preferred. (Winner must provide artwork in layer and can not flatten artwork.)
-Resolution: 300 dpi minimum
-Bleed: 1/16th (0.0625") inch from edge of label
-Color Mode: CMYK only or must be converted to CMYK for final production

Lastly, this is your project as a designer, artist, creator, this is essentially a piece of you that will be sold and known by thousands of people. I have no color scheme that I prefer, just use the template and follow the layout. If you have any further questions, please feel free to contact me at any time.
Updates

Quick note on the product and what it does: -Powerful, long lasting, harder erections -Works in a minutes and last for hours -Enhances sexual desire and drive Thank you for your ideas...

Project Deadline Extended
Reason: We decided to extent the project for a few more days to let the last few concepts come in. So far things are looking really good and we definitely have seen some amazing designs. Thank you for your hard work and amazing creativity. Looking forward to seeing what we have come in the next couple of day. Very respectfully, Brev

ONLY THREE DAYS LEFT!!!! Please submit your ideas as soon as possible. And as always, thank you for your help!!! V/r, Brev

Industry/Entity Type

Graphic Design

```html
<!DOCTYPE html>
<html lang="en">
<head>
<meta charset="utf-8">
<title>Velmora Crest – Horny Goat Weed 1600 Label</title>
<link href="https://fonts.googleapis.com/css2?family=Cormorant+Garamond:wght@500&family=Open+Sans:wght@400;600&display=swap" rel="stylesheet">
<style>
  :root {
    --backdrop-light: #f2f2f2;
    --backdrop-dark: #d6d6d6;
    --label-black: #141414;
    --label-edge: #1f1f1f;
    --ink-white: #f4f4f4;
    --ink-soft: #d9d9d9;
    --ink-muted: #a8a8a8;
    --rule: #bdbdbd;
  }
  * { margin: 0; padding: 0; box-sizing: border-box; }
  html, body { width: 1200px; height: 900px; overflow: hidden; }
  body {
    background: radial-gradient(ellipse at 50% 40%, var(--backdrop-light) 0%, var(--backdrop-dark) 100%);
    font-family: "Open Sans", Arial, sans-serif;
    position: relative;
  }
  .label {
    position: absolute;
    left: 60px; top: 240px;
    width: 1080px; height: 440px;
    background: radial-gradient(ellipse at 50% 50%, var(--label-edge) 0%, var(--label-black) 80%);
    color: var(--ink-white);
  }
  .side-panel {
    position: absolute;
    left: 40px; top: 70px;
    width: 200px;
    font-size: 10px;
    line-height: 1.6;
    color: var(--ink-soft);
  }
  .side-panel p { margin-bottom: 10px; }
  .storage-box {
    border: 1px solid var(--rule);
    border-radius: 3px;
    padding: 6px 8px;
    margin-top: 20px;
  }
  .facts {
    position: absolute;
    right: 50px; top: 50px;
    width: 200px; height: 300px;
    border: 2px solid var(--ink-white);
    padding: 10px 12px;
    font-size: 10px;
    line-height: 1.5;
    color: var(--ink-soft);
  }
  .facts-title {
    font-size: 17px;
    font-weight: 600;
    color: var(--ink-white);
    border-bottom: 1px solid var(--ink-white);
    padding-bottom: 4px;
    margin-bottom: 6px;
  }
  .facts-row {
    display: flex;
    justify-content: space-between;
    border-bottom: 1px solid var(--ink-muted);
    padding: 4px 0;
  }
  .facts-row--heavy { border-bottom: 4px solid var(--ink-white); font-weight: 600; color: var(--ink-white); }
  .facts-note { margin-top: 10px; color: var(--ink-muted); }
  .front {
    position: absolute;
    left: 300px; top: 0;
    width: 480px; height: 440px;
  }
  .brand {
    position: absolute;
    left: 0; right: 0; top: 50px;
    text-align: center;
    font-family: "Cormorant Garamond", Georgia, serif;
    font-weight: 500;
    font-size: 52px;
    letter-spacing: 1px;
    color: var(--ink-white);
  }
  .product {
    position: absolute;
    left: 40px; top: 175px;
  }
  .product-name {
    font-family: "Cormorant Garamond", Georgia, serif;
    font-weight: 500;
    font-size: 30px;
    line-height: 1.15;
    font-variant-numeric: lining-nums;
    color: var(--ink-white);
  }
  .claims {
    margin-top: 14px;
    font-size: 15px;
    line-height: 1.6;
    color: var(--ink-soft);
  }
  .category {
    font-size: 16px;
    letter-spacing: 0.5px;
    color: var(--ink-white);
  }
  .count {
    margin-top: 12px;
    font-size: 26px;
    color: var(--ink-white);
  }
  .figure-art {
    position: absolute;
    left: 330px; top: 150px;
    width: 130px; height: 260px;
  }
</style>
</head>
<body>
  <section class="label">
    <div class="side-panel">
      <p>Directions: Take 1 capsule daily with water.</p>
      <p>Do not exceed the stated dose. Keep out of reach of children.</p>
      <p>Consult a doctor before use.</p>
      <div class="storage-box">Store in a cool dry place.</div>
    </div>

    <div class="front">
      <h1 class="brand">Velmora Crest</h1>
      <div class="product">
        <h2 class="product-name">HORNY GOAT<br>WEED 1600</h2>
        <p class="claims">Max Strength<br>Pure and Potent</p>
        <p class="category">DIETARY SUPPLEMENT</p>
        <p class="count">60 Capsules</p>
      </div>
      <svg class="figure-art" role="img" aria-label="White line illustration of a woman's silhouette with long hair" viewBox="0 0 130 260">
        <defs>
          <radialGradient id="figureTone" cx="0.5" cy="0.4" r="0.6">
            <stop offset="0" stop-color="#3a3a3a"/>
            <stop offset="1" stop-color="#1a1a1a" stop-opacity="0"/>
          </radialGradient>
        </defs>
        <rect width="130" height="260" fill="url(#figureTone)"/>
      </svg>
    </div>

    <div class="facts">
      <h3 class="facts-title">Supplement Facts</h3>
      <p>Serving Size 2 Capsules</p>
      <p>Servings Per Container 30</p>
      <div class="facts-row facts-row--heavy"><span>Amount Per Serving</span><span>% Daily Value</span></div>
      <div class="facts-row"><span>Horny Goat Weed Extract</span><span>1600 mg</span></div>
      <p class="facts-note">Daily Value not established.</p>
      <p class="facts-note">Other ingredients: gelatin, rice flour.</p>
    </div>
  </section>
</body>
</html>
```